Pepper & Palm Business Card FUN & EXCITING

Here is the Information for the Card:
Jaswinder Bains (Ravi)
E: RaviBains@postlark.com
C: (480) 555-0147
www.PepperPalmLV.com

We don't want traditional Indian cliche, We a playful bold and fun business card.

Files: https://files.cloudvessel.net/share/folders/7TqRmXpZ2vKa9LwBn4YcHd3JsEf6UoGi?usp=share_link

https://files.cloudvessel.net/share/folders/4MzXaQ8rTw2YbNcVk6PsLe5GhJdR3FoU?usp=share_link

Target Market(s)

Las Vegas Local Restaurant

Industry/Entity Type

Indian Restaurant

Contact Information for Business Card

Name, Email, Cell Phone, Company Logo

```html
<!DOCTYPE html>
<html lang="en">
<head>
<meta charset="utf-8">
<title>Pepper &amp; Palm — Business Card</title>
<link href="https://fonts.googleapis.com/css2?family=Anton&family=Lobster&family=Old+Standard+TT:ital@1&display=swap" rel="stylesheet">
<style>
  :root {
    --bg: #2b2b2b;
    --orange: #f7a52a;
    --orange-deep: #ef7f2a;
    --cream: #fdf4d9;
    --pink: #e0709a;
    --ink: #111111;
    --icon-phone: #f08a2c;
    --icon-mail: #e68fb0;
    --icon-web: #4aaa4a;
    --icon-pin: #6b4a3a;
    --social-a: #3b5ba8;
    --social-b: #d6246e;
    --social-c: #d32323;
  }
  * { box-sizing: border-box; margin: 0; padding: 0; }
  html, body { width: 1200px; height: 689px; overflow: hidden; background: var(--bg); }
  .stage {
    width: 1200px; height: 689px;
    display: flex; align-items: center; justify-content: center; gap: 40px;
  }
  .card {
    position: relative; width: 540px; height: 309px;
    border-radius: 20px; overflow: hidden;
  }

  /* Logo side */
  .card--front { background: var(--orange); padding: 18px; }
  .front-panel {
    position: relative; width: 100%; height: 100%;
    background: var(--cream); border-radius: 30px;
  }
  .brand-art {
    position: absolute; left: 70px; top: 40px; width: 150px; height: 170px;
    border-radius: 50%;
    background: radial-gradient(circle at 50% 45%, #fff6e6 0%, #f3c998 55%, var(--orange-deep) 100%);
  }
  .brand-name {
    position: absolute; left: 230px; top: 36px; width: 260px;
    font-family: "Anton", sans-serif; font-size: 52px; line-height: 1;
    color: var(--ink); text-transform: uppercase; text-align: center;
  }
  .brand-city {
    position: absolute; left: 230px; top: 160px; width: 260px; text-align: center;
    font-family: "Anton", sans-serif; font-size: 15px; color: var(--ink);
    letter-spacing: 0.5px;
  }
  .tagline {
    position: absolute; left: 35px; top: 220px; width: 220px; text-align: center;
    font-family: "Old Standard TT", serif; font-style: italic; font-size: 14px; color: var(--ink);
  }
  .socials {
    position: absolute; right: 26px; bottom: 22px;
    display: flex; gap: 14px; list-style: none;
  }
  .social {
    display: flex; align-items: center; gap: 5px;
    font-family: "Anton", sans-serif; font-size: 12px; color: var(--ink);
  }
  .social-dot { width: 14px; height: 14px; border-radius: 50%; }
  .social-dot--a { background: var(--social-a); }
  .social-dot--b { background: var(--social-b); }
  .social-dot--c { background: var(--social-c); }

  /* Contact side */
  .card--back { background: var(--cream); }
  .back-swoosh { position: absolute; inset: 0; }
  .owner-name {
    position: absolute; left: 30px; top: 120px;
    font-family: "Lobster", cursive; font-size: 34px; font-weight: 400; color: var(--cream);
    white-space: nowrap;
    transform: rotate(-14deg); transform-origin: left top;
  }
  .mascot-art {
    position: absolute; left: 40px; top: 170px; width: 250px; height: 120px;
    border-radius: 60px;
    background: linear-gradient(90deg, #fff6e6 0%, #f3d2a6 50%, var(--orange-deep) 100%);
  }
  .contact-list {
    position: absolute; right: 24px; top: 150px; list-style: none;
    font-family: "Anton", sans-serif; font-size: 15px; color: var(--ink);
    text-align: right; line-height: 1.55;
  }
  .contact-item { display: flex; align-items: center; justify-content: flex-end; gap: 8px; }
  .contact-icon { width: 16px; height: 16px; border-radius: 50%; display: inline-flex; align-items: center; justify-content: center; flex: none; }
  .contact-icon svg { width: 10px; height: 10px; }
  .contact-icon--phone { background: var(--icon-phone); }
  .contact-icon--mail { background: var(--icon-mail); }
  .contact-icon--web { background: var(--icon-web); }
  .contact-icon--pin { background: var(--icon-pin); }
</style>
</head>
<body>
<main class="stage">

  <section class="card card--front" aria-label="Business card, logo side">
    <div class="front-panel">
      <div class="brand-art" role="img" aria-label="Cartoon mascots of a curry bowl and a naan walking together with hearts and sparkles"></div>
      <h1 class="brand-name">Pepper &amp; Palm</h1>
      <p class="brand-city">Sunhollow, NV</p>
      <p class="tagline">“A match made in heaven”</p>
      <ul class="socials">
        <li class="social"><span class="social-dot social-dot--a"></span>Friendnest</li>
        <li class="social"><span class="social-dot social-dot--b"></span>Snapframe</li>
        <li class="social"><span class="social-dot social-dot--c"></span>Tastebook</li>
      </ul>
    </div>
  </section>

  <section class="card card--back" aria-label="Business card, contact side">
    <svg class="back-swoosh" viewBox="0 0 540 309" preserveAspectRatio="none" aria-hidden="true">
      <path d="M0 0 H540 V40 C470 120 300 120 150 180 C80 210 30 250 0 290 Z" fill="var(--orange)"/>
      <path d="M540 40 C470 120 300 120 150 180 C300 130 470 140 540 60 Z" fill="var(--pink)"/>
      <path d="M150 180 C80 210 30 250 0 290 V300 C40 250 90 215 170 185 Z" fill="var(--orange-deep)"/>
    </svg>
    <h2 class="owner-name">Jaswinder Bains (Ravi)</h2>
    <div class="mascot-art" role="img" aria-label="Cartoon mascots of a curry bowl and a naan walking with hearts and sparkles"></div>
    <ul class="contact-list">
      <li class="contact-item">(480) 555-0147
        <span class="contact-icon contact-icon--phone"><svg viewBox="0 0 10 10"><rect x="3" y="1" width="4" height="8" rx="1" fill="none" stroke="#fff" stroke-width="1"/></svg></span></li>
      <li class="contact-item">RaviBains@postlark.com
        <span class="contact-icon contact-icon--mail"><svg viewBox="0 0 10 10"><rect x="1" y="2.5" width="8" height="5" fill="none" stroke="#fff" stroke-width="1"/><path d="M1 2.5 L5 6 L9 2.5" fill="none" stroke="#fff" stroke-width="1"/></svg></span></li>
      <li class="contact-item">PepperPalmLV.com
        <span class="contact-icon contact-icon--web"><svg viewBox="0 0 10 10"><circle cx="5" cy="5" r="3.5" fill="none" stroke="#fff" stroke-width="1"/><path d="M1.5 5 H8.5 M5 1.5 V8.5" stroke="#fff" stroke-width="0.8"/></svg></span></li>
      <li class="contact-item">Sunhollow, NV
        <span class="contact-icon contact-icon--pin"><svg viewBox="0 0 10 10"><path d="M5 9 C2 5.5 2 2 5 1.5 C8 2 8 5.5 5 9 Z" fill="#fff"/></svg></span></li>
    </ul>
  </section>

</main>
</body>
</html>
```